Buch-/eBook-Cover für Sachbuch gesucht
Zielgruppe
We're selfpublishing nonfiction books. Interested are adults - mostly man (age range: 25-50) - who want to learn more about leadership at their workplaces.
Aufgabenstellung
The design should be clean and simple, title easy to read, good color contrast (the cover has to stand out from an white background).

```html
<!DOCTYPE html>
<html lang="en">
<head>
<meta charset="utf-8">
<title>Leadership – Book Cover</title>
<link rel="stylesheet" href="https://fonts.googleapis.com/css2?family=Archivo+Black&family=Saira+Condensed:wght@600&display=swap">
<style>
  :root {
    --paper: #ffffff;
    --sky-blue: #2ba3dc;
    --deep-indigo: #2f2b63;
    --magenta: #e0197b;
    --teal: #78c2cb;
    --cloud: #aedde6;
    --cloud-soft: rgba(174, 221, 230, 0);
    --sun-yellow: #f3e36a;
  }
  html, body {
    margin: 0;
    padding: 0;
    width: 848px;
    height: 1200px;
    overflow: hidden;
    background: var(--paper);
  }
  .cover {
    position: relative;
    width: 848px;
    height: 1200px;
    background: var(--paper);
    overflow: hidden;
  }
  .cloud-band-top {
    position: absolute;
    left: 0; top: 0;
    width: 470px; height: 115px;
    background: linear-gradient(180deg, var(--cloud) 0%, var(--cloud) 55%, var(--cloud-soft) 100%);
    border-bottom-right-radius: 60px;
  }
  .cloud-band-side {
    position: absolute;
    left: 0; top: 770px;
    width: 300px; height: 430px;
    background: linear-gradient(90deg, var(--cloud) 0%, var(--cloud) 60%, var(--cloud-soft) 100%);
    border-top-right-radius: 140px;
  }
  .cloud-band-bottom {
    position: absolute;
    left: 0; bottom: 0;
    width: 848px; height: 150px;
    background: linear-gradient(0deg, var(--cloud) 0%, var(--cloud) 55%, var(--cloud-soft) 100%);
  }
  .climbers-art {
    position: absolute;
    left: 445px; top: 28px;
    width: 185px; height: 282px;
    background: linear-gradient(160deg, rgba(47,43,99,0.18), rgba(243,227,106,0.25));
    border-radius: 8px;
  }
  .sprout-art {
    position: absolute;
    left: 145px; top: 428px;
    width: 64px; height: 70px;
    background: rgba(174, 221, 230, 0.7);
    border-radius: 50% 50% 8px 8px;
  }
  .bird-art {
    position: absolute;
    left: 120px; top: 925px;
    width: 130px; height: 60px;
    background: linear-gradient(90deg, rgba(243,227,106,0.9), rgba(243,227,106,0.5));
    border-radius: 30px;
  }
  .title {
    position: absolute;
    left: 0; top: 0;
    width: 848px; height: 720px;
  }
  .title text {
    font-family: "Archivo Black", "Arial Black", sans-serif;
    font-size: 250px;
  }
  .title .line-light { fill: var(--sky-blue); }
  .title .line-dark { fill: var(--deep-indigo); }
  .subtitle {
    position: absolute;
    left: 123px; top: 690px;
    margin: 0;
    font-family: "Saira Condensed", "Arial Narrow", sans-serif;
    font-weight: 600;
    font-size: 62px;
    line-height: 68px;
    color: var(--magenta);
    letter-spacing: -0.5px;
  }
  .author {
    position: absolute;
    left: 370px; top: 930px;
    margin: 0;
    font-family: "Saira Condensed", "Arial Narrow", sans-serif;
    font-weight: 600;
    font-size: 66px;
    color: var(--teal);
    letter-spacing: -1px;
  }
</style>
</head>
<body>
  <main class="cover">
    <div class="cloud-band-top" role="img" aria-label="Pale blue clouds along the top edge"></div>
    <div class="cloud-band-side" role="img" aria-label="Pale blue clouds rising along the left side"></div>
    <div class="cloud-band-bottom" role="img" aria-label="Pale blue clouds along the bottom edge"></div>

    <div class="climbers-art" role="img" aria-label="Illustration of business people roped together climbing the title, the leader planting a yellow flag"></div>
    <div class="sprout-art" role="img" aria-label="Small pale blue plant sprout illustration"></div>
    <div class="bird-art" role="img" aria-label="Yellow bird in flight illustration"></div>

    <svg class="title" viewBox="0 0 848 720" aria-label="Leadership">
      <text class="line-light" x="118" y="326" textLength="452" lengthAdjust="spacingAndGlyphs">LEA</text>
      <text class="line-dark" x="255" y="502" textLength="485" lengthAdjust="spacingAndGlyphs">DER</text>
      <text class="line-light" x="118" y="684" textLength="532" lengthAdjust="spacingAndGlyphs">SHIP</text>
    </svg>

    <h2 class="subtitle">Fostering Growth<br>and Inspiring Excellence</h2>
    <p class="author">Daniel Fairbanks</p>
  </main>
</body>
</html>
```